Site for entrepreneurs/small businesses needs Logo, Homepage

Looking for a logo, either an icon, or stylized text, or a combination of both, and a home page design which fits with it. The logo will be for use on the public website as well as for printed collateral (business cards, post cards, brochures and various other marketing materials).

The site is called Orbitwell (Orbitwell.example). This is to be a national, and eventually an international brand. The new service will provide an easy-to-use platform for entrepreneurs to build their business and web presence together in an integrated way which allows them to focus on their core competency.

The site/service will be dead-simple to use, A/B/C, 1/2/3. We will want some sort of "Get started for FREE" promotional space to collect the person's email address with multiple points of interest which guide the user back to this one call to action: sign up for free. We will feature editorial/blog stories, customer testimonials, and present several key features the the reader just can't live without if they are starting a new business.

Criteria:
* Refer to our comparable sites/logos in the design document attached
* Incorporate our color scheme (but complementary colors welcome)
* No Serif fonts!
* No photo-realistic elements for logo
* Logo must present well in gray scale and/or black/white (for printed materials)
* Strokes/borders that are wider to promote simplicity (vs. thin/precise lines which promote technical complexity)

Inspirations:
* Creative/Custom (but legible) fonts
* Excitement, energetic, jumping for joy
* Karate / Ninja / Power / Precision
* Dance Moves
* Regional influences: California, Silicon Valley, West Coast, Surf City, Beaches, Sunset
* Simple/easy, no-brainer solutions

Target Market(s)

Small Businesses / Entrepreneurs

Logo Text

Orbitwell or Orbitwell.example

Number of Pages Required

1 page

Font styles to use
Sans Serif
Decorative

Requirements
Must have
• See the attached style guide (PDF)

```html
<!DOCTYPE html>
<html lang="en">
<head>
<meta charset="utf-8">
<title>Orbitwell — Build your business and web presence together</title>
<link rel="stylesheet" href="https://fonts.googleapis.com/css2?family=Mulish:wght@400;600;700;800&display=swap">
<style>
:root{
  --purple-deep:#3a0d6b;
  --purple:#5b1a96;
  --purple-bright:#7a2bc0;
  --orange:#f7941d;
  --orange-dark:#e8780c;
  --ink:#2b2b33;
  --muted:#8a8a96;
  --line:#e4e4ea;
  --white:#ffffff;
}
*{box-sizing:border-box;margin:0;padding:0}
html,body{width:1200px;height:4696px;overflow:hidden}
body{position:relative;font-family:"Mulish",Arial,sans-serif;color:var(--ink);background:var(--white)}
.backdrop{position:absolute;left:0;top:0;width:1200px;height:4696px}
.abs{position:absolute}
.btn{display:inline-block;background:var(--orange);color:var(--white);font-weight:700;font-size:14px;letter-spacing:.5px;text-transform:uppercase;padding:12px 26px;border-radius:24px;box-shadow:0 4px 10px rgba(247,148,29,.35)}
.btn-small{font-size:12px;padding:9px 20px}
.section-title{font-size:44px;font-weight:600;color:var(--ink)}
.section-sub{font-size:11px;letter-spacing:1px;text-transform:uppercase;color:var(--muted);text-align:center}
.body-text{font-size:15px;line-height:27px;color:var(--muted)}

/* header */
.site-header{position:absolute;left:0;top:0;width:1200px;height:90px;z-index:5}
.brand{left:80px;top:22px;color:var(--white);font-size:34px;font-weight:800;display:flex;align-items:center;gap:10px}
.brand-dot{width:16px;height:16px;border-radius:50%;background:var(--orange)}
.main-nav{right:60px;top:44px;display:flex;gap:28px;font-size:14px;font-weight:600;color:var(--white);white-space:nowrap}
.hero-title{left:100px;top:200px;font-size:58px;font-weight:700;color:var(--white)}
.hero-text{left:100px;top:280px;width:440px;font-size:20px;line-height:30px;color:var(--white)}
.hero-btn{left:100px;top:392px}
.hero-art{left:700px;top:96px;width:380px;height:380px;border-radius:190px 190px 190px 190px;background:linear-gradient(180deg,#6f2fb3,#4a5fb8 60%,#2e7fc4)}

/* service cards */
.service-card{width:300px;height:430px;background:var(--white);box-shadow:0 8px 28px rgba(40,10,80,.18);text-align:center;padding:40px 34px 0;z-index:2}
.service-icon{width:68px;height:68px;border-radius:50%;margin:0 auto 20px;background:linear-gradient(135deg,#e94e4e,#f7941d 50%,#2aa7a0)}
.service-card h3{font-size:22px;line-height:27px;font-weight:700;margin-bottom:18px}
.service-card p{font-size:13px;line-height:22px;color:var(--muted);margin-bottom:26px}

/* who we are */
.who-title{left:100px;top:1070px}
.who-text{left:100px;top:1148px;width:420px}
.who-btn{left:100px;top:1400px}
.who-art{left:640px;top:1100px;width:440px;height:290px;border-radius:8px;background:linear-gradient(135deg,#dfe3ee,#9aa6c4 55%,#3d4a6b)}

/* key features */
.features-art{left:180px;top:1600px;width:340px;height:370px;border-radius:8px;background:linear-gradient(135deg,#eef0f4,#c7ccd8 50%,#e3564e)}
.features-title{left:570px;top:1624px}
.feature-list{left:570px;top:1704px;list-style:none;font-size:14px;line-height:25px;color:var(--muted)}
.feature-list li{display:flex;align-items:center;gap:12px}
.feature-list svg{flex:none}
.features-btn{left:584px;top:1914px}

/* testimonials */
.testimonials-title{left:0;top:2080px;width:1200px;text-align:center;font-size:40px}
.testimonial{width:440px;height:300px;background:var(--white);box-shadow:0 8px 28px rgba(40,10,80,.15);padding:30px 34px 0 90px;z-index:2}
.quote-mark{position:absolute;left:34px;top:18px;font-size:72px;font-weight:800;color:var(--purple);line-height:1}
.testimonial p{font-size:14px;line-height:23px;color:var(--muted)}
.author{display:flex;align-items:center;gap:16px;margin-top:40px;margin-left:-46px}
.avatar{width:66px;height:66px;border-radius:50%;background:linear-gradient(135deg,#c9a27a,#6b4b35)}
.author strong{display:block;font-size:14px;color:var(--purple)}
.author span{font-size:12px;color:var(--muted)}
.dots{left:0;top:2526px;width:1200px;display:flex;justify-content:center;gap:10px}
.dots i{width:10px;height:10px;border-radius:50%;background:#cfc6dc}
.dots i.active{background:var(--purple)}

/* blog */
.blog-title{left:0;top:2644px;width:1200px;text-align:center}
.blog-sub{left:0;top:2722px;width:1200px}
.blog-card{width:312px;height:400px;background:var(--white);box-shadow:0 8px 28px rgba(40,10,80,.16);z-index:2}
.blog-image{height:220px}
.blog-card p{font-size:14px;line-height:21px;color:var(--muted);padding:22px 22px 0}
.blog-meta{display:flex;align-items:center;justify-content:space-between;padding:22px 22px 0}
.blog-author{display:flex;align-items:center;gap:10px;font-size:12px;font-weight:800}
.blog-author i{width:38px;height:38px;border-radius:50%;background:linear-gradient(135deg,#c9a27a,#5c3f2e)}

/* signup */
.signup{left:150px;top:3350px;width:900px;height:650px;background:var(--white);border-radius:24px;box-shadow:0 8px 34px rgba(40,10,80,.16);text-align:center;padding-top:70px}
.signup h2{font-size:40px;font-weight:600}
.signup .section-sub{margin-top:16px}
.signup-form{width:500px;margin:40px auto 0;display:flex;flex-direction:column;gap:18px;text-align:left}
.field{height:50px;border:1px solid var(--line);border-radius:6px;padding:16px 18px;font-size:13px;color:var(--muted)}
.field-message{height:96px}
.signup .btn{margin-top:34px}

/* newsletter */
.divider{left:100px;top:4120px;width:1000px;height:2px;background:linear-gradient(90deg,var(--purple),var(--orange))}
.talk{left:100px;top:4186px;width:440px;font-size:22px;line-height:32px;font-weight:600}
.email-box{left:640px;top:4190px;width:440px;height:56px;border-radius:28px;border:1px solid var(--line);box-shadow:0 4px 18px rgba(40,10,80,.12);background:var(--white);display:flex;align-items:center;justify-content:space-between;padding:0 24px;font-size:13px;color:var(--muted)}

/* footer */
.footer-brand{left:88px;top:4452px;font-size:38px;font-weight:800;color:var(--white);display:flex;align-items:center;gap:10px}
.footer-links{top:4418px;list-style:none;font-size:14px;line-height:28px;color:var(--white)}
.social{left:920px;top:4410px;display:flex;gap:14px}
.social i{width:34px;height:34px;border-radius:50%;border:2px solid var(--white)}
.copyright{left:412px;top:4622px;font-size:12px;color:rgba(255,255,255,.75)}
.chat{right:40px;top:4640px;font-size:13px;font-weight:700;color:var(--white)}
</style>
</head>
<body>

<svg class="backdrop" viewBox="0 0 1200 4696" aria-hidden="true">
  <defs>
    <linearGradient id="violet" x1="0" y1="0" x2="1" y2="1">
      <stop offset="0" stop-color="#6a22a8"/>
      <stop offset="1" stop-color="#3a0d6b"/>
    </linearGradient>
  </defs>
  <polygon points="0,0 1200,0 1200,540 0,820" fill="url(#violet)"/>
  <polygon points="1200,600 1200,1240 1010,1090 1100,650" fill="url(#violet)"/>
  <polygon points="0,1150 70,1220 40,1690 0,1700" fill="url(#violet)"/>
  <polygon points="1200,1880 900,1960 1010,2520 1200,2580" fill="url(#violet)"/>
  <polygon points="0,2700 150,2770 110,3330 0,3350" fill="url(#violet)"/>
  <path d="M0,4400 C300,4330 600,4350 880,4320 C1020,4305 1120,4290 1200,4270 L1200,4696 L0,4696 Z" fill="url(#violet)"/>
</svg>

<section class="hero">
  <div class="abs hero-art" role="img" aria-label="Illustration of a businessman riding a rocket launching into space"></div>
  <h1 class="abs hero-title">Orbitwell</h1>
  <p class="abs hero-text">At vero eos et accusamus et iusto odio dignissimos ducimus qui blanditiis praese voluptatum deleniti atque corrupti</p>
  <span class="abs btn hero-btn">Learn More</span>
</section>

<header class="site-header">
  <div class="abs brand"><span class="brand-dot"></span>Orbitwell</div>
  <nav class="abs main-nav"><span>Home</span><span>About Us</span><span>Services</span><span>Who We are</span><span>Our Solution</span><span>Contact Us</span></nav>
</header>

<section class="services">
  <article class="abs service-card" style="left:100px;top:512px">
    <div class="service-icon" role="img" aria-label="Target icon illustration"></div>
    <h3>At vero eos et accusamus et iusto</h3>
    <p>Sed ut perspiciatis unde omnis iste natus error sit voluptatem accusantium doloremque totam rem aperiam eaque ipsa.</p>
    <span class="btn btn-small">Read More</span>
  </article>
  <article class="abs service-card" style="left:452px;top:512px">
    <div class="service-icon" role="img" aria-label="Growth chart icon illustration"></div>
    <h3>At vero eos et accusamus et iusto</h3>
    <p>Sed ut perspiciatis unde omnis iste natus error sit voluptatem accusantium doloremque totam rem aperiam eaque ipsa.</p>
    <span class="btn btn-small">Read More</span>
  </article>
  <article class="abs service-card" style="left:800px;top:512px">
    <div class="service-icon" role="img" aria-label="Team settings icon illustration"></div>
    <h3>At vero eos et accusamus et iusto</h3>
    <p>Sed ut perspiciatis unde omnis iste natus error sit voluptatem accusantium doloremque totam rem aperiam eaque ipsa.</p>
    <span class="btn btn-small">Read More</span>
  </article>
</section>

<section class="who">
  <h2 class="abs section-title who-title">Who We Are</h2>
  <p class="abs body-text who-text">At vero eos et accusamus et iusto odio dignissimos ducimus qui blanditiis praesentium voluptatum deleniti atque corrupti quos dolores et quas molestias excepturi sint occaecati cupiditate non provident, similique sunt in culpa qui officia deserunt mollitia animi, id est laborum et dolorum fuga. Et harum quidem rerum facilis est et expedita distinctio.</p>
  <span class="abs btn who-btn">Read More</span>
  <div class="abs who-art" role="img" aria-label="Illustration of a team meeting around a conference table with a presentation screen"></div>
</section>

<section class="features">
  <div class="abs features-art" role="img" aria-label="Illustration of a businessman in front of gears and a circuit network"></div>
  <h2 class="abs section-title features-title">Key Features</h2>
  <ul class="abs feature-list">
    <li><svg width="12" height="10" viewBox="0 0 12 10"><path d="M1 5l3.5 3.5L11 1" stroke="#f7941d" stroke-width="2" fill="none"/></svg>At vero eos et accusamus et iusto odio dignissimos ducimus</li>
    <li><svg width="12" height="10" viewBox="0 0 12 10"><path d="M1 5l3.5 3.5L11 1" stroke="#f7941d" stroke-width="2" fill="none"/></svg>Praesentium voluptatum deleniti atque corrupti quos dolores</li>
    <li><svg width="12" height="10" viewBox="0 0 12 10"><path d="M1 5l3.5 3.5L11 1" stroke="#f7941d" stroke-width="2" fill="none"/></svg>Nam libero tempore, cum soluta nobis est eligendi optio</li>
    <li><svg width="12" height="10" viewBox="0 0 12 10"><path d="M1 5l3.5 3.5L11 1" stroke="#f7941d" stroke-width="2" fill="none"/></svg>Temporibus autem quibusdam et aut officiis debitis aut rerum</li>
    <li><svg width="12" height="10" viewBox="0 0 12 10"><path d="M1 5l3.5 3.5L11 1" stroke="#f7941d" stroke-width="2" fill="none"/></svg>Et harum quidem rerum facilis est et expedita distinctio</li>
    <li><svg width="12" height="10" viewBox="0 0 12 10"><path d="M1 5l3.5 3.5L11 1" stroke="#f7941d" stroke-width="2" fill="none"/></svg>Sed ut perspiciatis unde omnis iste natus error sit voluptatem</li>
  </ul>
  <span class="abs btn features-btn">Read More</span>
</section>

<section class="testimonials">
  <h2 class="abs section-title testimonials-title">Customer Testimonials</h2>
  <blockquote class="abs testimonial" style="left:160px;top:2164px">
    <span class="quote-mark">“</span>
    <p>At harum quidem rerum facilis est et distinctio. Nam libero tempore, cum soluta nobis est eligendi optio cumque nihil impedit quo minus.</p>
    <div class="author"><i class="avatar" role="img" aria-label="Customer portrait"></i><div><strong>Mara Ellison</strong><span>Praesentium voluptatum</span></div></div>
  </blockquote>
  <blockquote class="abs testimonial" style="left:640px;top:2164px">
    <span class="quote-mark">“</span>
    <p>At harum quidem rerum facilis est et distinctio. Nam libero tempore, cum soluta nobis est eligendi optio cumque nihil impedit quo minus.</p>
    <div class="author"><i class="avatar" role="img" aria-label="Customer portrait"></i><div><strong>Mara Ellison</strong><span>Praesentium voluptatum</span></div></div>
  </blockquote>
  <div class="abs dots"><i class="active"></i><i></i><i></i></div>
</section>

<section class="blog">
  <h2 class="abs section-title blog-title">Our Blog</h2>
  <p class="abs section-sub blog-sub">Sed ut perspiciatis unde omnis iste natus error sit voluptatem</p>
  <article class="abs blog-card" style="left:100px;top:2820px">
    <div class="blog-image" role="img" aria-label="Illustration of a man working at a laptop on a desk" style="background:linear-gradient(135deg,#2fb5a0,#1f8a7c)"></div>
    <p>Lorem ipsum dolor sit amet, consectetur adipiscing elit, sed do eiusmod tempor.</p>
    <div class="blog-meta"><span class="blog-author"><i role="img" aria-label="Author portrait"></i>DEAN COLBY</span><span class="btn btn-small">View Details</span></div>
  </article>
  <article class="abs blog-card" style="left:444px;top:2820px">
    <div class="blog-image" role="img" aria-label="Illustration of analytics charts and a growth dashboard" style="background:linear-gradient(135deg,#f4f1e8,#9cc7e6 55%,#f7941d)"></div>
    <p>Lorem ipsum dolor sit amet, consectetur adipiscing elit, sed do eiusmod tempor.</p>
    <div class="blog-meta"><span class="blog-author"><i role="img" aria-label="Author portrait"></i>DEAN COLBY</span><span class="btn btn-small">View Details</span></div>
  </article>
  <article class="abs blog-card" style="left:788px;top:2820px">
    <div class="blog-image" role="img" aria-label="Illustration of a group of business people talking" style="background:linear-gradient(135deg,#eceef2,#b7bfcf 55%,#5a6478)"></div>
    <p>Lorem ipsum dolor sit amet, consectetur adipiscing elit, sed do eiusmod tempor.</p>
    <div class="blog-meta"><span class="blog-author"><i role="img" aria-label="Author portrait"></i>DEAN COLBY</span><span class="btn btn-small">View Details</span></div>
  </article>
</section>

<section class="abs signup">
  <h2>Get started for FREE</h2>
  <p class="section-sub">Sed ut perspiciatis unde omnis iste natus error sit voluptatem</p>
  <div class="signup-form">
    <div class="field">User Name</div>
    <div class="field">Email Address</div>
    <div class="field">Phone No</div>
    <div class="field field-message">Message</div>
  </div>
  <span class="btn">Sign Up for Free</span>
</section>

<section class="newsletter">
  <div class="abs divider"></div>
  <p class="abs talk">Let's talk about how we can help you better understand your users.</p>
  <div class="abs email-box"><span>Enter Your Email Address</span><svg width="22" height="12" viewBox="0 0 22 12"><path d="M0 6h19M14 1l5 5-5 5" stroke="#3a0d6b" stroke-width="2" fill="none"/></svg></div>
</section>

<footer>
  <div class="abs footer-brand"><span class="brand-dot"></span>Orbitwell</div>
  <ul class="abs footer-links" style="left:412px"><li>About</li><li>Blog</li><li>Careers</li><li>Terms Of Services</li></ul>
  <ul class="abs footer-links" style="left:592px"><li>Faq</li><li>Privacy policy</li><li>Sitemap</li></ul>
  <div class="abs social"><i></i><i></i><i></i><i></i></div>
  <p class="abs copyright">© 2016 Copyrights Orbitwell All Rights Reserved</p>
  <span class="abs chat">Chat</span>
</footer>

</body>
</html>
```